Lotstallmart.com Webpage Design

Design Brief for lotstallmart.com (Copy of Brief also in attached Word file)

Name of Website- lotstallmart.com (existing logo and look & feel of website to be changed)

Logo - Finalised. The logo files are attached with the brief as “logo.jpeg”. The “Blue- Grey” version of the logo is for use on lighter backgrounds and the “Orange-White” version of the logo is for use on darker backgrounds. (A full Black version of the logo is also attached). Both versions may be used in different parts of the website. All attached files are in .png format.
Status - The website in functional and is undergoing user trials. However, we want to improve the look & feel of the website so at it seems
a. cotemporary,
b. Easy to Navigate
c. professional and
d. Vibrant.

Please visit ‘lotstallmart.com’ to check out the website and its functionalities – please use it only as a reference for the features & functions to be provided, however the designer should use a ‘Free Hand’ in designing the composition of various parts of the webpage without getting too influenced by the existing design

Objective of the Website ‘lotstallmart.com –
a. It is a portal focussed on listing of ‘Retail’ specific real-estate properties by developers, owners and realty brokers. The properties shall listed under the following four categories-
i. Retail Malls
ii. Shopping Complexes
iii. High-street shops
iv. Retail Warehouses
*refer lotstallmart.com for better clarity

b. The abovementioned properties shall be listed either for ‘Sale’ or ‘rent\lease’ or both

c. Users shall visit the site in case they wish to acquire a retail \ shop space either on ‘sale’ or ‘rent’. These Users would be able to specify the ‘Search Criteria’ through the tool-bars provided on the website – the ‘Search Criteria’ shall comprise of ‘Type of space category’, ‘City’, ‘Locality’, transaction type ie ‘Rent \ Sale’ and ‘Area Range’

d. The main revenue model for the website shall be listing fee ( or advertising charges ) payable by those listing their properties on the website.

Three Main Pages of Website (lotstallmart.com) that need to be designed -
a. Main Home Page (visit the web link - http://lotstallmart.com/ ) - The main home page has the “Search Toolbar” for specifying of Search Criteria by the User. It shall also have the following features & functions-
i. Main Advertising Banner
ii. Featured Projects
iii. New Launches
iv. Toolbar with buttons – ‘Advertise with Us’, ‘Listings Alert’, ‘Mart Wizards’, ‘Advertiser Login’

b. Property Listings Page (visit the web link - http://lotstallmart.com/gurgaon-in-india ) - The List of property options that match the Criteria specified by the ‘User’ get displayed on this page.

c. Property Detail Page - When the ‘User’ clicks on the “More….” Button on the ‘Property Listings Page’ (given in point b. above) the web page with the details of the property opens. (For Example – visit the web link - http://lotstallmart.com/vorne-Shopping-Complex-vorne-quadrion-gurgaon-636 )

Note:- Please refer to attached ‘Shopping’ related images the designer may use them on the website to provide a look & feel of retail if required – either separately or rotate in a single window

Target Market(s)

Retailers & Investors looking for retail space, Real Estate Brokers, Developers

Industry/Entity Type

Advertising

Number of Pages Required

3 page

Requirements
Must have
• Refer to existing site lotstallmart.com -- all the existing functionalities are a must have.
Nice to have
• The Designer may use the retail related images on the website if required for making it more vibrant. Refer attached images Shopping(1-6).jpg

```html
<!DOCTYPE html>
<html lang="en">
<head>
<meta charset="utf-8">
<title>Lotstallmart.com – Retail Space Portal</title>
<link href="https://fonts.googleapis.com/css2?family=Open+Sans:wght@400;600;700&family=Noto+Serif:ital@1&display=swap" rel="stylesheet">
<style>
:root{
  --blue:#1f9df1;
  --blue-mid:#1a8fe3;
  --blue-deep:#0d5e9f;
  --blue-text:#1b8fe0;
  --red:#d43d24;
  --grey-bar:#4b4b4b;
  --ink:#222;
  --line:#d8d8d8;
  --white:#fff;
  --foot-top:#5a5a5a;
  --foot-bot:#7b7b7b;
}
*{box-sizing:border-box;margin:0;padding:0}
html,body{width:1200px;height:3822px;overflow:hidden}
body{font-family:"Open Sans",Arial,sans-serif;color:var(--ink);background:var(--white);position:relative}
section,header,footer{position:relative;width:1200px}

/* city bar */
.city-bar{height:30px;background:var(--grey-bar)}
.city-bar ul{list-style:none;display:flex;gap:22px;position:absolute;left:184px;top:7px;font-size:11px;color:#eee}

/* header */
.site-header{height:153px;background:var(--white)}
.brand{position:absolute;left:184px;top:16px;display:flex;align-items:center;gap:10px}
.brand-dot{width:40px;height:40px;border-radius:50%;background:var(--blue)}
.brand-name{font-size:28px;font-weight:700;color:var(--blue-deep);line-height:1}
.brand-tag{position:absolute;left:234px;top:62px;font-size:9px;color:#888}
.help{position:absolute;left:468px;top:50px;font-size:14px}
.help b{font-weight:700}
.list-prop{position:absolute;right:183px;top:68px;font-size:12px;color:#333;text-decoration:underline}
.main-nav{position:absolute;left:184px;top:91px;width:833px;height:62px;display:flex;border-bottom:3px solid var(--blue)}
.main-nav a{display:flex;flex-direction:column;justify-content:center;padding:0 14px;font-size:15px;font-weight:600;color:#333;text-decoration:none;line-height:1.2}
.main-nav a small{font-size:10px;font-weight:400;color:#666}
.main-nav .home{background:var(--blue);color:#fff;width:78px}
.main-nav .login{background:var(--red);color:#fff}
.main-nav .login small{color:#fdd}

/* hero */
.hero{height:701px;background:var(--blue)}
.search-box{position:absolute;left:184px;top:30px;width:334px;height:383px;background:#3da9f1;border:1px solid #7cc5f6}
.search-head{background:var(--blue-deep);color:#fff;text-align:center;padding:8px 0 6px;font-size:16px;font-weight:700;line-height:1.3}
.search-head span{display:block;font-size:12px;font-weight:400;text-decoration:underline}
.formats{display:grid;grid-template-columns:1fr 1fr;gap:8px 6px;padding:14px 22px 10px;font-size:13px;color:#fff}
.formats label{display:flex;align-items:center;gap:6px}
.box{width:14px;height:14px;background:#fff;border:1px solid #9bd}
.field{margin:0 22px 10px;height:36px;background:#fff;border:1px solid var(--blue-mid);font-size:13px;color:#444;display:flex;align-items:center;justify-content:space-between;padding-left:10px}
.field .drop{width:26px;height:100%;border-left:1px solid var(--blue-mid);display:flex;align-items:center;justify-content:center}
.btn-search{margin:14px 22px 0;height:46px;background:var(--blue-deep);color:#fff;font-size:15px;display:flex;align-items:center;justify-content:center}
.hero-photo{position:absolute;left:520px;top:30px;width:497px;height:383px;background:linear-gradient(120deg,#eae4dc 0%,#f0b04a 40%,#e46a24 62%,#c23c38 80%,#d9d1c6 100%)}
.hero-caption{position:absolute;right:0;bottom:0;width:100%;height:40px;background:linear-gradient(90deg,rgba(0,0,0,0),rgba(0,0,0,.45));color:#fff;font-size:16px;text-align:right;padding:9px 16px}
.formats-row{position:absolute;left:184px;top:455px;width:833px;display:flex;justify-content:space-between}
.fmt{display:flex;align-items:center;gap:12px;color:#fff;font-size:17px;line-height:1.2;width:190px}
.fmt .ring{width:62px;height:62px;border:2px solid #fff;border-radius:50%;display:flex;align-items:center;justify-content:center;flex-shrink:0}
.hero-text{position:absolute;left:184px;top:550px;width:833px;color:#fff;text-align:center;font-size:15px;line-height:25px}
.hero-text a{color:#fff;text-decoration:underline}

/* cards */
.featured{height:530px}
.section-title{position:absolute;left:184px;display:flex;align-items:center;gap:14px}
.section-title h2{font-size:25px;font-weight:400;color:#222}
.section-title span{border-left:1px solid #999;padding-left:12px;font-size:12px;height:44px;display:flex;align-items:center}
.cards{position:absolute;left:184px;width:833px;display:flex;justify-content:space-between}
.card{width:197px;height:332px;border:1px solid var(--line);background:#fff;text-align:center;font-size:13px}
.card h3{font-size:13px;font-weight:700;padding:10px 0 7px;color:#222}
.card.active{border:2px solid #4db2f5}
.card.active h3{color:var(--blue-text)}
.card-photo{height:144px;margin:0 6px;background:linear-gradient(180deg,#9cc7e6 0%,#d4d9d8 55%,#8a7a66 100%)}
.card .type{padding-top:14px;color:#333}
.card .pin{margin:14px auto 4px;display:block}
.card .loc{color:var(--blue-text);font-weight:700}
.card .view{margin-top:14px;color:#666;font-size:12px}
.card.active .view{color:var(--red)}
.arrow{position:absolute;width:34px;height:34px;border-radius:50%;display:flex;align-items:center;justify-content:center}
.arrow.dark{background:#555}
.arrow.light{background:#ddd}

/* wizards */
.wizards{height:502px;background:var(--blue)}
.notch{position:absolute;left:577px;top:0;width:0;height:0;border-left:23px solid transparent;border-right:23px solid transparent;border-top:22px solid #fff}
.wizards h2{position:absolute;top:92px;width:100%;text-align:center;color:#fff;font-size:24px;font-weight:700}
.wizards p{position:absolute;left:250px;top:140px;width:700px;text-align:center;color:#fff;font-size:15px;line-height:25px}
.wizards .dash{position:absolute;left:588px;top:216px;width:24px;height:3px;background:#fff}
.inp{position:absolute;border:1px solid #9fd3f8;background:var(--blue-mid);color:#fff;font-size:13px;padding:6px 12px}
.btn-dark{position:absolute;background:var(--blue-deep);color:#fff;font-size:14px;display:flex;align-items:center;justify-content:center}

/* launches + testimonial */
.launches{height:922px}
.avatar{position:absolute;left:560px;top:555px;width:80px;height:80px;border-radius:50%;background:radial-gradient(circle,#e9a460,#b86a3c);border:4px solid #fff;box-shadow:0 0 0 1px #ddd}
.quote{position:absolute;left:262px;top:657px;width:676px;text-align:center;font-family:"Noto Serif",Georgia,serif;font-style:italic;font-size:15px;line-height:23px;color:#666}
.quote .mark{color:var(--blue-text)}
.quote-rule{position:absolute;left:570px;top:764px;width:60px;height:1px;background:#bbb}
.quote-name{position:absolute;top:782px;width:100%;text-align:center;font-family:"Noto Serif",Georgia,serif;font-style:italic;font-size:14px;color:#555}
.quote-name b{color:var(--blue-text);font-weight:400}
.dots{position:absolute;left:583px;top:841px;display:flex;gap:4px}
.dots i{width:10px;height:10px;border-radius:50%;background:#4a7aa6}
.dots i:first-child{background:#888}

/* alert & editor */
.panels{height:632px}
.panel{position:absolute;top:0;height:530px;padding:62px 44px 0}
.panel h2{font-size:27px;font-weight:400;color:#fff;margin-bottom:14px}
.panel.alert{left:184px;width:410px;background:var(--blue)}
.panel.editor{left:604px;width:413px;background:var(--red)}
.panel .lead{color:#fff;font-size:12px;line-height:17px;width:300px}
.pfield{width:282px;height:38px;background:#fff;border:1px solid #ccc;font-size:12px;color:#555;display:flex;align-items:center;justify-content:space-between;padding-left:12px}
.pfield .drop{width:24px;height:100%;border-left:1px solid #bbb;display:flex;align-items:center;justify-content:center}
.hint{color:#fff;font-size:10px;margin:3px 0 18px}
.fold{position:absolute;right:0;bottom:0;display:block}
.editor-photo{width:294px;height:164px;background:linear-gradient(180deg,#bfc8cc 0%,#8a7f76 50%,#5d5650 100%);border:3px solid #fff;margin:8px 0 14px}

/* footer */
.site-footer{position:relative;height:268px;background:linear-gradient(180deg,var(--foot-top),var(--foot-bot))}
.foot-col{position:absolute;top:60px;list-style:none;color:#fff;font-size:12px;line-height:30px}
.follow{position:absolute;left:522px;top:56px;width:180px;color:#fff;font-size:12px;text-align:center}
.follow .rule{display:flex;align-items:center;gap:8px}
.follow .rule i{flex:1;height:1px;background:#fff}
.socials{display:flex;gap:9px;justify-content:center;margin-top:16px}
.socials span{width:34px;height:34px;border-radius:50%;border:2px solid #fff}
.copy{position:absolute;left:795px;top:60px;color:#fff;font-size:12px;line-height:18px}
.foot-brand{position:absolute;left:795px;top:120px;display:flex;align-items:center;gap:8px}
.foot-brand .dot{width:32px;height:32px;border-radius:50%;background:#fff}
.foot-brand b{color:#fff;font-size:24px;font-weight:700}
.bottom-bar{position:relative;height:84px;background:var(--blue);color:#fff;font-size:12px;text-align:center;padding-top:24px;line-height:18px}
.bottom-pin{position:absolute;left:591px;top:-12px}
</style>
</head>
<body>

<nav class="city-bar" aria-label="Cities">
  <ul><li>Bangalore</li><li>Chennai</li><li>Greater Noida</li><li>Gurgaon</li><li>Hyderabad</li><li>Jaipur</li><li>Khanna</li><li>Kolkatta</li><li>Mumbai</li><li>Noida</li><li>Pune</li><li>Surat</li></ul>
</nav>

<header class="site-header">
  <div class="brand"><span class="brand-dot"></span><span class="brand-name">lotstallmart</span></div>
  <div class="brand-tag">India's leading portal for retail space</div>
  <div class="help">Call for Help : <b>000-000-0000</b></div>
  <div class="list-prop">List Your Property Here</div>
  <nav class="main-nav">
    <a class="home" href="#">Home</a>
    <a href="#">Advertise with Us<small>Standard Listing - FREE</small></a>
    <a href="#">Mart Wizards<small>Shop Search Services</small></a>
    <a href="#">Listing Alert</a>
    <a class="login" href="#">Advertiser Login<small>Ready Registered</small></a>
    <a href="#">New Advertiser - Register</a>
  </nav>
</header>

<section class="hero">
  <form class="search-box">
    <div class="search-head">Select Retail Format<span>Meaning of Retail Format</span></div>
    <div class="formats">
      <label><span class="box"><svg width="12" height="12" viewBox="0 0 12 12"><path d="M2 6l3 3 5-7" stroke="#0d5e9f" stroke-width="2" fill="none"/></svg></span>Retail Malls</label>
      <label><span class="box"></span>High Street Shops</label>
      <label><span class="box"></span>Shopping Complex</label>
      <label><span class="box"></span>Retail Warehouses</label>
    </div>
    <div class="field">Enter Keywords:</div>
    <div class="field">Sale Or Rent Or Both:<span class="drop"><svg width="10" height="6"><path d="M0 0l5 6 5-6z" fill="#0d5e9f"/></svg></span></div>
    <div class="field">Select City:<span class="drop"><svg width="10" height="6"><path d="M0 0l5 6 5-6z" fill="#0d5e9f"/></svg></span></div>
    <div class="field">Select Locality/Micro-Market.<span class="drop"><svg width="10" height="6"><path d="M0 0l5 6 5-6z" fill="#0d5e9f"/></svg></span></div>
    <div class="btn-search">SEARCH NOW</div>
  </form>
  <div class="hero-photo" role="img" aria-label="Banner photo: a shopper in orange carrying colourful shopping bags">
    <div class="hero-caption">Shops at Elm Row Bangalore</div>
  </div>

  <div class="formats-row">
    <div class="fmt"><span class="ring"><svg width="28" height="28" viewBox="0 0 28 28" fill="none" stroke="#fff" stroke-width="2"><path d="M4 24V10l10-6 10 6v14z"/><path d="M11 24v-7h6v7"/></svg></span>Retail<br>Malls</div>
    <div class="fmt"><span class="ring"><svg width="28" height="28" viewBox="0 0 28 28" fill="none" stroke="#fff" stroke-width="2"><rect x="5" y="4" width="18" height="20"/><path d="M9 9h3M16 9h3M9 14h3M16 14h3M12 24v-5h4v5"/></svg></span>Shopping<br>Complexes</div>
    <div class="fmt"><span class="ring"><svg width="28" height="28" viewBox="0 0 28 28" fill="none" stroke="#fff" stroke-width="2"><path d="M5 11h18l-2 13H7z"/><path d="M10 11a4 4 0 0 1 8 0"/></svg></span>High-Street<br>Shops</div>
    <div class="fmt"><span class="ring"><svg width="28" height="28" viewBox="0 0 28 28" fill="none" stroke="#fff" stroke-width="2"><path d="M3 6h4l3 12h12l2-9H9"/><circle cx="12" cy="22" r="1.5"/><circle cx="20" cy="22" r="1.5"/></svg></span>Retail<br>Warehouses</div>
  </div>

  <p class="hero-text">The Lotstallmart.com is a Specialised Web based platform for Retail Space, featuring properties across India under various formats such as Retail Malls, Shopping Complexes, High-street Shops. Also featured are Retail Warehouses which provide the logistic back-end for the retail business. Lotstallmart.com is useful to various category of users as follows- a. Devel &nbsp;<a href="#">Learn More &gt;&gt;</a></p>
</section>

<section class="featured">
  <div class="section-title" style="top:52px"><h2>Featured Retail Projects</h2><span>Across India</span></div>
  <div class="cards" style="top:127px">
    <article class="card active"><h3>Veltora</h3><div class="card-photo" role="img" aria-label="Photo of a mid-rise shopping complex building"></div><div class="type">Shopping Complex</div><svg class="pin" width="14" height="18" viewBox="0 0 14 18"><path d="M7 0a7 7 0 0 0-7 7c0 5 7 11 7 11s7-6 7-11a7 7 0 0 0-7-7z" fill="#1b8fe0"/><circle cx="7" cy="7" r="2.5" fill="#fff"/></svg><div class="loc">Surat - Althan</div><div class="view">View the Listing &gt;</div></article>
    <article class="card"><h3>Kestrel Arcade</h3><div class="card-photo" role="img" aria-label="Photo of a high street retail building lit at dusk"></div><div class="type">Shopping Complex</div><svg class="pin" width="14" height="18" viewBox="0 0 14 18"><path d="M7 0a7 7 0 0 0-7 7c0 5 7 11 7 11s7-6 7-11a7 7 0 0 0-7-7z" fill="#1b8fe0"/><circle cx="7" cy="7" r="2.5" fill="#fff"/></svg><div class="loc">Surat - Althan</div><div class="view">View the Listing &gt;</div></article>
    <article class="card"><h3>Zarin Heights</h3><div class="card-photo" role="img" aria-label="Photo of a tall commercial tower"></div><div class="type">Shopping Complex</div><svg class="pin" width="14" height="18" viewBox="0 0 14 18"><path d="M7 0a7 7 0 0 0-7 7c0 5 7 11 7 11s7-6 7-11a7 7 0 0 0-7-7z" fill="#1b8fe0"/><circle cx="7" cy="7" r="2.5" fill="#fff"/></svg><div class="loc">Surat - Althan</div><div class="view">View the Listing &gt;</div></article>
    <article class="card"><h3>Orbis Plaza</h3><div class="card-photo" role="img" aria-label="Photo of a glass-fronted retail mall"></div><div class="type">Shopping Complex</div><svg class="pin" width="14" height="18" viewBox="0 0 14 18"><path d="M7 0a7 7 0 0 0-7 7c0 5 7 11 7 11s7-6 7-11a7 7 0 0 0-7-7z" fill="#1b8fe0"/><circle cx="7" cy="7" r="2.5" fill="#fff"/></svg><div class="loc">Surat - Althan</div><div class="view">View the Listing &gt;</div></article>
  </div>
  <span class="arrow dark" style="left:124px;top:286px"><svg width="10" height="12"><path d="M8 0L1 6l7 6" stroke="#fff" stroke-width="2.5" fill="none"/></svg></span>
  <span class="arrow light" style="left:1044px;top:286px"><svg width="10" height="12"><path d="M2 0l7 6-7 6" stroke="#fff" stroke-width="2.5" fill="none"/></svg></span>
</section>

<section class="wizards">
  <span class="notch"></span>
  <h2>Mart Wizards</h2>
  <p>Post your Retail Space requirement with us and our experts shall get back with suitable options and even help you in your transaction. This is a Free Service!</p>
  <span class="dash"></span>
  <div class="inp" style="left:311px;top:232px;width:288px;height:41px">Enter Email</div>
  <div class="inp" style="left:604px;top:232px;width:285px;height:41px">Mobile</div>
  <div class="inp" style="left:311px;top:280px;width:578px;height:90px">Message</div>
  <div class="btn-dark" style="left:545px;top:387px;width:110px;height:39px">Send</div>
</section>

<section class="launches">
  <div class="section-title" style="top:78px"><h2>Featured New Launches</h2><span>Across India</span></div>
  <div class="cards" style="top:155px">
    <article class="card active"><h3>Veltora</h3><div class="card-photo" role="img" aria-label="Photo of a mid-rise shopping complex building"></div><div class="type">Shopping Complex</div><svg class="pin" width="14" height="18" viewBox="0 0 14 18"><path d="M7 0a7 7 0 0 0-7 7c0 5 7 11 7 11s7-6 7-11a7 7 0 0 0-7-7z" fill="#1b8fe0"/><circle cx="7" cy="7" r="2.5" fill="#fff"/></svg><div class="loc">Surat - Althan</div><div class="view">View the Listing &gt;</div></article>
    <article class="card"><h3>Kestrel Arcade</h3><div class="card-photo" role="img" aria-label="Photo of a high street retail building lit at dusk"></div><div class="type">Shopping Complex</div><svg class="pin" width="14" height="18" viewBox="0 0 14 18"><path d="M7 0a7 7 0 0 0-7 7c0 5 7 11 7 11s7-6 7-11a7 7 0 0 0-7-7z" fill="#1b8fe0"/><circle cx="7" cy="7" r="2.5" fill="#fff"/></svg><div class="loc">Surat - Althan</div><div class="view">View the Listing &gt;</div></article>
    <article class="card"><h3>Zarin Heights</h3><div class="card-photo" role="img" aria-label="Photo of a tall commercial tower"></div><div class="type">Shopping Complex</div><svg class="pin" width="14" height="18" viewBox="0 0 14 18"><path d="M7 0a7 7 0 0 0-7 7c0 5 7 11 7 11s7-6 7-11a7 7 0 0 0-7-7z" fill="#1b8fe0"/><circle cx="7" cy="7" r="2.5" fill="#fff"/></svg><div class="loc">Surat - Althan</div><div class="view">View the Listing &gt;</div></article>
    <article class="card"><h3>Orbis Plaza</h3><div class="card-photo" role="img" aria-label="Photo of a glass-fronted retail mall"></div><div class="type">Shopping Complex</div><svg class="pin" width="14" height="18" viewBox="0 0 14 18"><path d="M7 0a7 7 0 0 0-7 7c0 5 7 11 7 11s7-6 7-11a7 7 0 0 0-7-7z" fill="#1b8fe0"/><circle cx="7" cy="7" r="2.5" fill="#fff"/></svg><div class="loc">Surat - Althan</div><div class="view">View the Listing &gt;</div></article>
  </div>
  <span class="arrow light" style="left:124px;top:313px"><svg width="10" height="12"><path d="M8 0L1 6l7 6" stroke="#fff" stroke-width="2.5" fill="none"/></svg></span>
  <span class="arrow dark" style="left:1044px;top:313px"><svg width="10" height="12"><path d="M2 0l7 6-7 6" stroke="#fff" stroke-width="2.5" fill="none"/></svg></span>

  <div class="avatar" role="img" aria-label="Customer portrait"></div>
  <span class="arrow dark" style="left:184px;top:685px"><svg width="10" height="12"><path d="M8 0L1 6l7 6" stroke="#fff" stroke-width="2.5" fill="none"/></svg></span>
  <span class="arrow light" style="left:983px;top:685px"><svg width="10" height="12"><path d="M2 0l7 6-7 6" stroke="#fff" stroke-width="2.5" fill="none"/></svg></span>
  <p class="quote"><span class="mark">“</span> Duis aute irure dolor in reprehenderit in voluptate velit esse cillum dolore eu fugiat nulla pariatur. Excepteur sint occaecat cupidatat non proident, sunt in culpa qui officia deserunt mollit anim id est laborum. <span class="mark">”</span></p>
  <span class="quote-rule"></span>
  <div class="quote-name"><b>Meera Talwar</b> - Mumbai</div>
  <div class="dots"><i></i><i></i><i></i></div>
</section>

<section class="panels">
  <div class="panel alert">
    <h2>Listing Alert</h2>
    <p class="lead">Suscribe for Fortnightly Email update on New Listings @ Lotstallmart</p>
    <div class="pfield" style="margin-top:20px">Enter Email</div>
    <div class="pfield" style="margin-top:18px">Select Question<span class="drop"><svg width="10" height="6"><path d="M0 0l5 6 5-6z" fill="#555"/></svg></span></div>
    <div class="hint">(select retail format of interest)</div>
    <div class="pfield">Select City<span class="drop"><svg width="10" height="6"><path d="M0 0l5 6 5-6z" fill="#555"/></svg></span></div>
    <div class="hint">(select cities of interest)</div>
    <div class="btn-dark" style="position:relative;width:168px;height:40px;margin-top:26px">Subscribe</div>
    <svg class="fold" width="46" height="46" viewBox="0 0 46 46"><path d="M46 0L0 46h46z" fill="#fff"/><path d="M46 0L0 46L0 10Q0 0 10 0z" fill="#a3a3a3"/></svg>
  </div>
  <div class="panel editor">
    <h2>Editor's Choice</h2>
    <div class="editor-photo" role="img" aria-label="Photo of shoppers walking along a busy retail street"></div>
    <p class="lead">A "Select" Listing of Retail Properties Handpicked by our Editors based on their own positive evaluation on parameters &amp; attributes such as Design Concept, Location, Developer, Success Potential. So Read On to Check Out for yourself ...</p>
    <div class="btn-dark" style="position:relative;width:110px;height:40px;margin-top:18px">Send</div>
    <svg class="fold" width="46" height="46" viewBox="0 0 46 46"><path d="M46 0L0 46h46z" fill="#fff"/><path d="M46 0L0 46L0 10Q0 0 10 0z" fill="#a3a3a3"/></svg>
  </div>
</section>

<footer>
  <div class="site-footer">
    <span class="notch"></span>
    <ul class="foot-col" style="left:184px"><li>About Us</li><li>Privacy Policy</li><li>Terms of Use</li><li>Contact Us</li><li>Site Map</li></ul>
    <ul class="foot-col" style="left:322px"><li>Retail Malls</li><li>Shopping Complex</li><li>High Street Shops</li><li>Retail Warehouses</li></ul>
    <div class="follow">
      <div class="rule"><i></i>Follow us<i></i></div>
      <div class="socials" aria-label="Social links"><span></span><span></span><span></span><span></span></div>
    </div>
    <div class="copy">Copyright © 2015 Bharat Mart Holdings<br>All rights reserved</div>
    <div class="foot-brand"><span class="dot"></span><b>lotstallmart</b></div>
  </div>
  <div class="bottom-bar">
    <svg class="bottom-pin" width="18" height="24" viewBox="0 0 14 18"><path d="M7 0a7 7 0 0 0-7 7c0 5 7 11 7 11s7-6 7-11a7 7 0 0 0-7-7z" fill="#111"/><circle cx="7" cy="7" r="2.5" fill="#fff"/></svg>
    Bharat Mart Holdings : Unit 118, 2nd Floor, Lorem Ipsum is simply, Sector x, Gurgaon - 122050<br>
    Phone : 000-000-0000 &nbsp;· &nbsp;Fax : 000 - 000 - 0000
  </div>
</footer>

</body>
</html>
```